Quillbrook Climate Business Card Design

Design new, 2 sides, business cards for a residential and light commercial heating, air conditioning contractor.

Target Market(s)

Homeowners, small businesses

Industry/Entity Type

Business

Contact Information for Business Card

Dominic Westerhall
Phone - 862-415-2736
Email
Address - PO box 518
Brightwater NJ 07912
Website - www.QuillbrookClimateLLC.example

Requirements
Must have
• logo, company colors, standard size with no die cut, so I can use nova stamp

```html
<!DOCTYPE html>
<html lang="en">
<head>
<meta charset="utf-8">
<title>Quillbrook Climate Business Card</title>
<link rel="stylesheet" href="https://fonts.googleapis.com/css2?family=Barlow+Semi+Condensed:wght@400;500;600&family=Roboto:wght@400&display=swap">
<style>
  :root {
    --backdrop: #e9e9e9;
    --card-black: #0b0b0d;
    --card-white: #f6f6f4;
    --maroon: #7e2331;
    --maroon-dark: #5e1a25;
    --cream: #f3dfa0;
    --icon-red: #c8352e;
    --ink: #2a2a2a;
    --muted: #4a4a4a;
  }
  * { margin: 0; padding: 0; box-sizing: border-box; }
  html, body {
    width: 1200px; height: 576px; overflow: hidden;
    background: var(--backdrop);
  }
  .canvas { position: relative; width: 1200px; height: 576px; }
  .card {
    position: absolute; top: 138px; width: 484px; height: 294px; overflow: hidden;
  }
  .card--front { left: 81px; background: var(--card-black); }
  .card--back { left: 602px; width: 482px; height: 292px; background: var(--card-white); }

  .brand-name {
    position: absolute; left: 0; right: 0; text-align: center;
    font-family: "Barlow Semi Condensed", sans-serif; font-weight: 600;
    font-size: 38px; letter-spacing: 0.5px; line-height: 1;
  }
  .card--front .brand-name { top: 115px; color: var(--cream); }
  .card--back .brand-name { top: 83px; color: var(--maroon); }

  .service-band {
    position: absolute; left: 0; right: 0; top: 247px; height: 27px;
    background: var(--maroon);
    display: flex; align-items: center; justify-content: center;
    font-family: "Roboto", sans-serif; font-size: 12px; color: var(--cream);
    gap: 6px;
  }

  .person { position: absolute; left: 26px; top: 188px; }
  .person-name {
    font-family: "Barlow Semi Condensed", sans-serif; font-weight: 600;
    font-size: 18px; color: var(--maroon-dark); line-height: 1.1;
  }
  .person-title {
    font-family: "Roboto", sans-serif; font-size: 10.5px; color: var(--muted);
    margin-top: 4px;
  }

  .contact-list {
    position: absolute; left: 266px; top: 190px; list-style: none;
  }
  .contact-item {
    display: flex; align-items: center; height: 17px;
    font-family: "Barlow Semi Condensed", sans-serif; font-weight: 500;
    font-size: 12.5px; color: var(--ink); white-space: nowrap;
  }
  .contact-icon { width: 11px; height: 11px; margin-right: 8px; fill: var(--icon-red); }
  .bottom-bar {
    position: absolute; left: 0; right: 0; bottom: 0; height: 7px; background: var(--maroon);
  }
</style>
</head>
<body>
<main class="canvas">
  <section class="card card--front" aria-label="Card front">
    <div class="brand-name">Quillbrook Climate</div>
    <div class="service-band">
      <span>Residential &amp; Light Commercial Heating</span>
      <span>• Air Conditioning Contractor</span>
    </div>
  </section>

  <section class="card card--back" aria-label="Card back">
    <div class="brand-name">Quillbrook Climate</div>
    <div class="person">
      <div class="person-name">Dominic Westerhall</div>
      <div class="person-title">Managing Director</div>
    </div>
    <ul class="contact-list">
      <li class="contact-item">
        <svg class="contact-icon" viewBox="0 0 12 12"><path d="M1 4c0-2 2-3 5-3s5 1 5 3v1H8V4H4v1H1zM3 6h6l2 4v1H1v-1z"/></svg>
        862-415-2736
      </li>
      <li class="contact-item">
        <svg class="contact-icon" viewBox="0 0 12 12"><path d="M0 2h12v8H0zM1 3l5 4 5-4" stroke="#fff" stroke-width="1"/></svg>
        info@QuillbrookClimateLLC.example
      </li>
      <li class="contact-item">
        <svg class="contact-icon" viewBox="0 0 12 12"><circle cx="6" cy="6" r="5.5"/><path d="M0.5 6h11M6 0.5v11M2 3h8M2 9h8" stroke="#fff" stroke-width="0.7" fill="none"/></svg>
        www.QuillbrookClimateLLC.example
      </li>
      <li class="contact-item">
        <svg class="contact-icon" viewBox="0 0 12 12"><path d="M6 0a4 4 0 0 1 4 4c0 3-4 8-4 8S2 7 2 4a4 4 0 0 1 4-4z"/><circle cx="6" cy="4" r="1.5" fill="#fff"/></svg>
        PO box 518 Brightwater NJ 07912
      </li>
    </ul>
    <div class="bottom-bar"></div>
  </section>
</main>
</body>
</html>
```